Church needs a street sign design

We're a small church located in Silicon Valley, California. Our website is https://www.vgtmarlowfield.org/ and our address is 4817 Ferrow Ave, San Jose, California, 95873. You can look up our location on Google Maps to see the sign from Street View. I have uploaded an image of the street sign as well. The marquee, the top section of the sign, and the separating line between them both will be removed. We're seeking a design for a new backlit acrylic insert that will go on the front of the light box and the back of the lightbox. The acrylic sign will fill the entire external frame. In the future, we may build a decorative wood frame around the structural legs, as visualized in one of the uploaded files. The church's brand colors are: #003366 (dark blue), #ff6600 (vibrant orange), #228b22 (forest green). I have also uploaded the church's logo assets. Our primary font is Montserrat and the secondary is Poppins. You can deviate from these colors/fonts if the sign is still coherent with the rest of our branding. Our branding values are mission, truth, passion, and community (please do not put those words on the sign! They are just intended to guide the look of the design). The sign dimensions are 96" by 47.5". Keep in mind that the sign will be backlit on a busy street side. It will also be positioned next to an old-looking church building. We do NOT want a sign that looks traditional, old, or antiquated. Instead, we want a modern-looking sign that pairs well with our old building while helping it look more modern too. We would also like the web address clearly visible on the sign: vgtmarlowfield.org. If you have any questions, just let me know!

```html
<!DOCTYPE html>
<html lang="en">
<head>
<meta charset="utf-8">
<title>Marlowfield Community Church – Street Sign</title>
<link rel="stylesheet" href="https://fonts.googleapis.com/css2?family=Montserrat:wght@500;600;800;900&family=Poppins:wght@600&family=Kaushan+Script&display=swap">
<style>
  :root {
    --backdrop: #aab0b8;
    --brand-blue: #003366;
    --brand-orange: #ff6600;
    --deep-orange: #ff3d00;
    --sun-gold: #f9b64a;
    --sun-rose: #d9487a;
    --sky-violet: #5a3d8c;
    --white: #ffffff;
  }
  * { margin: 0; padding: 0; box-sizing: border-box; }
  html, body { width: 980px; height: 1200px; overflow: hidden; }
  body { background: var(--backdrop); position: relative; }

  .sign {
    position: absolute;
    left: 40px; top: 377px;
    width: 900px; height: 445px;
    background: var(--brand-blue);
    overflow: hidden;
    box-shadow: 0 10px 24px rgba(0,0,0,0.18);
  }

  .sign-top {
    position: absolute; left: 0; top: 0;
    width: 900px; height: 183px;
    background: var(--brand-orange);
  }
  .top-accent {
    position: absolute; left: 647px; top: 0;
    width: 253px; height: 183px;
    background: linear-gradient(100deg, rgba(255,102,0,0) 0%, #ff7a10 25%, #ff5a00 60%, var(--deep-orange) 100%);
  }

  .church-name {
    position: absolute; left: 37px; top: 62px;
    display: flex; align-items: center; gap: 12px;
    color: var(--white);
    font-family: "Montserrat", sans-serif;
    font-weight: 600;
    font-size: 21px;
    line-height: 1.15;
    letter-spacing: 0.02em;
    text-transform: uppercase;
  }
  .church-name .mark {
    width: 16px; height: 16px;
    border: 3px solid var(--white);
    flex: none;
  }

  .headline {
    position: absolute; left: 377px; top: 28px;
    color: var(--white);
    font-family: "Montserrat", sans-serif;
    font-weight: 900;
    font-size: 80px;
    line-height: 68px;
    letter-spacing: -0.01em;
    text-transform: uppercase;
  }

  .sunrise-scene {
    position: absolute; left: 0; top: 183px;
    width: 400px; height: 262px;
    background:
      radial-gradient(circle at 34% 42%, rgba(255,240,190,0.95) 0%, var(--sun-gold) 14%, rgba(217,72,122,0.75) 38%, rgba(90,61,140,0.55) 58%, rgba(0,51,102,0) 78%),
      linear-gradient(90deg, var(--sky-violet) 0%, rgba(0,51,102,0) 100%);
  }

  .mission {
    position: absolute; left: 375px; top: 212px;
  }
  .mission-script {
    display: block;
    color: var(--brand-orange);
    font-family: "Kaushan Script", cursive;
    font-size: 50px;
    line-height: 52px;
    margin-left: 2px;
  }
  .mission-main {
    display: block;
    color: var(--white);
    font-family: "Poppins", sans-serif;
    font-weight: 600;
    font-size: 74px;
    line-height: 70px;
    letter-spacing: -0.01em;
    margin-top: -8px;
  }

  .purpose {
    position: absolute; left: 720px; top: 229px;
    color: var(--white);
    font-family: "Montserrat", sans-serif;
    font-size: 29px;
    line-height: 27px;
    text-transform: uppercase;
  }
  .purpose .light { display: block; font-weight: 500; letter-spacing: 0.09em; }
  .purpose .bold { display: block; font-weight: 800; letter-spacing: 0.05em; }

  .web-pill {
    position: absolute; left: 375px; top: 368px;
    width: 489px; height: 41px;
    border-radius: 21px;
    background: var(--brand-orange);
    display: flex; align-items: center; justify-content: center;
    color: var(--white);
    font-family: "Montserrat", sans-serif;
    font-weight: 600;
    font-size: 24px;
    letter-spacing: 0.12em;
  }
  .web-pill .domain { font-weight: 800; }
</style>
</head>
<body>
  <div class="sign">
    <div class="sign-top">
      <div class="top-accent" role="img" aria-label="Large decorative cross emblem in deep orange and red tones"></div>
      <div class="church-name">
        <span class="mark"></span>
        <span>Marlowfield<br>Community Church</span>
      </div>
      <h1 class="headline">Making<br>Disciples</h1>
    </div>

    <div class="sunrise-scene" role="img" aria-label="Photo of a cross silhouetted against a sunrise sky with clouds and grass"></div>

    <p class="mission">
      <span class="mission-script">&amp; Helping the</span>
      <span class="mission-main">Helpless</span>
    </p>

    <p class="purpose">
      <span class="light">For the</span>
      <span class="light">Glory</span>
      <span class="bold">of</span>
      <span class="bold">Christ</span>
    </p>

    <div class="web-pill">www.<span class="domain">vgtmarlowfield</span>.org</div>
  </div>
</body>
</html>
```